Website Design Request - Management Consulting Firm

We need a Website designed for an IT Management Staffing and Recruiting firm called TRAVENOK based in San Francisco.

The firm is an high-end technology staffing agency. Our focus is on quality and high-caliber candidates rather than quantity.

The website will have two main home pages. One for the recruiter and another on for the candidates.

The website needs to optimize for mobile devices as well.

I have attached few mock-ups that I have done just to show what I am thinking. The UI needs to be very clean, fluid, and it needs to have a modern, rustic, professional feel to it.

Target Market(s)

Technology Manager, Director, VP, CIO of Companies that have $4b-10b dollar revenue. Such as larkspurdwellings.example , https://www.velmorian.example/, quillnet.example, zib.example

Industry/Entity Type

Management Consulting

Number of Pages Required

5+ page

Font styles to use
Sans Serif

Colors
f37122
ffffff

Requirements
Must have
• Please review mock-ups for suggestions
Nice to have
Should not have

```html
<!DOCTYPE html>
<html lang="en">
<head>
<meta charset="utf-8">
<title>TRAVENOK – IT Project Management Jobs</title>
<link href="https://fonts.googleapis.com/css2?family=Montserrat:wght@400;500;600&family=Open+Sans:wght@400;600&display=swap" rel="stylesheet">
<style>
:root{
  --orange:#f37122;
  --orange-soft:#fd7d3f;
  --ink:#1e1e1e;
  --text:#555;
  --black:#050505;
  --white:#fff;
  --footer:#f6f6f6;
  --rule:#cfcfcf;
}
*{box-sizing:border-box;margin:0;padding:0}
html,body{width:878px;height:1200px;overflow:hidden}
body{position:relative;background:var(--white);font-family:"Open Sans",sans-serif;color:var(--ink)}
.abs{position:absolute}
.brand{font-family:"Montserrat",sans-serif;font-weight:600;color:var(--orange);letter-spacing:1px}
.site-header{left:0;top:0;width:878px;height:83px}
.site-header .brand{left:69px;top:24px;font-size:26px}
.brand-tag{left:70px;top:55px;font-family:"Montserrat",sans-serif;font-size:7px;letter-spacing:.6px;color:#333}
.nav{font-family:"Montserrat",sans-serif;font-size:11px;color:#222;top:37px}
.nav-home{left:388px;top:30px;width:67px;height:25px;border:1px solid var(--orange);border-radius:13px;color:var(--orange);text-align:center;line-height:23px}
.hero{left:0;top:83px;width:878px;height:372px;background:linear-gradient(180deg,#6d6a66 0%,#4d4a47 55%,#3a3836 100%)}
.hero-title{left:0;width:878px;top:190px;text-align:center;font-family:"Montserrat",sans-serif;font-weight:600;font-size:18.5px;color:var(--white)}
.hero-sub{left:0;width:878px;top:219px;text-align:center;font-size:13.5px;color:var(--white)}
.hero-input{left:210px;top:255px;width:457px;height:36px;background:var(--white);border-radius:2px;padding-left:14px;line-height:36px;font-size:12px;color:#333}
.hero-btn{left:357px;top:311px;width:164px;height:34px;background:var(--orange);border-radius:17px;text-align:center;line-height:34px;font-weight:600;font-size:13.5px;color:var(--white)}
.hero-arrow{top:256px;width:21px;height:21px;border-radius:50%;background:#111;border:1px solid #999}
.hero-foot{top:401px;font-size:13.5px;color:var(--white)}
.hero-foot u{text-underline-offset:2px}
.tab{top:455px;height:63px;line-height:63px;text-align:center;font-family:"Montserrat",sans-serif;font-size:19px;color:var(--white)}
.tab-how{left:0;width:438px;background:var(--black)}
.tab-why{left:438px;width:440px;background:var(--orange-soft)}
.section-title{left:0;width:878px;top:575px;text-align:center;font-family:"Montserrat",sans-serif;font-size:19px;color:#111}
.feature-icon{width:81px;height:81px;border-radius:50%;border:1px solid #cfcfcf}
.feature-icon svg{position:absolute;left:24px;top:24px}
.feature-title{font-family:"Montserrat",sans-serif;font-weight:500;font-size:12px;color:#222}
.feature-text{font-size:9px;line-height:14px;color:var(--text);width:250px;text-align:justify}
.upload{left:0;top:873px;width:878px;height:114px;background:linear-gradient(90deg,#3d4046 0%,#4b4f57 50%,#3a3c42 100%);border-left:3px solid #222}
.upload-title{left:0;width:878px;top:940px;text-align:center;font-family:"Montserrat",sans-serif;font-size:21px;color:var(--white)}
.site-footer{left:0;top:987px;width:878px;height:213px;background:var(--footer)}
.site-footer .brand{left:69px;top:1063px;font-size:19px}
.footer-tag{left:69px;top:1083px;font-family:"Montserrat",sans-serif;font-size:5.5px;letter-spacing:.5px;color:#333}
.footer-head{top:1032px;font-family:"Montserrat",sans-serif;font-size:10px;color:#333}
.footer-text{font-size:8px;line-height:16px;color:var(--text)}
.mail-input{left:443px;top:1087px;width:108px;height:24px;border:1px solid #ccc;background:var(--white);font-size:8.5px;line-height:22px;padding-left:6px;color:#666}
.mail-btn{left:551px;top:1087px;width:41px;height:24px;background:var(--orange);color:var(--white);font-size:8.5px;line-height:24px;text-align:center}
.social{top:1063px;width:18px;height:18px;border-radius:3px;background:#666}
.footer-rule{left:67px;top:1152px;width:748px;height:1px;background:var(--rule)}
.copyright{left:0;width:878px;top:1171px;text-align:center;font-size:9px;color:#333}
</style>
</head>
<body>
<header class="site-header abs">
  <div class="brand abs">TRAVENOK</div>
  <div class="brand-tag abs">PROJECT MANAGEMENT CONSULTING</div>
  <div class="nav nav-home abs">
    <svg width="9" height="8" viewBox="0 0 10 9" style="vertical-align:-1px"><path d="M5 0 L10 4.5 H8.5 V9 H6 V6 H4 V9 H1.5 V4.5 H0 Z" fill="#f37122"/></svg> HOME
  </div>
  <div class="nav abs" style="left:479px">PROFESSIONALS</div>
  <div class="nav abs" style="left:600px">EMPLOYERS</div>
  <div class="nav abs" style="left:697px">SIGN IN</div>
  <div class="nav abs" style="left:771px">SIGN UP</div>
</header>

<section class="hero abs" role="img" aria-label="Photo of professionals seated in a row waiting for interviews"></section>
<h1 class="hero-title abs">LOOKING FOR IT PROJECT MANAGEMENT JOBS?</h1>
<p class="hero-sub abs">Upload your resume, accept interview requests, get offers</p>
<div class="hero-input abs">Your Email Address</div>
<div class="hero-btn abs">Get Offers Now</div>
<div class="hero-arrow abs" style="left:53px"><svg width="21" height="21" viewBox="0 0 21 21"><path d="M12 6 L8 10.5 L12 15" stroke="#fff" stroke-width="2" fill="none"/></svg></div>
<div class="hero-arrow abs" style="left:805px"><svg width="21" height="21" viewBox="0 0 21 21"><path d="M9 6 L13 10.5 L9 15" stroke="#fff" stroke-width="2" fill="none"/></svg></div>
<p class="hero-foot abs" style="left:269px">Looking for talents?</p>
<p class="hero-foot abs" style="left:420px"><u>See how it works for employers</u></p>

<div class="tab tab-how abs">HOW IT WORKS ?</div>
<div class="tab tab-why abs">WHY US ?</div>

<h2 class="section-title abs">WHY PROFESSIONALS LOVE US</h2>

<div class="feature-icon abs" style="left:66px;top:631px">
  <svg width="32" height="32" viewBox="0 0 32 32"><rect x="2" y="5" width="28" height="18" rx="2" fill="#f37122"/><rect x="5" y="8" width="22" height="12" fill="#fff"/><rect x="13" y="23" width="6" height="4" fill="#f37122"/><rect x="9" y="27" width="14" height="2" fill="#f37122"/></svg>
</div>
<h3 class="feature-title abs" style="left:158px;top:641px">GET PAID MORE</h3>
<p class="feature-text abs" style="left:158px;top:660px">On average, TRAVENOK candidates get upto 20% more for their skills. Our Talent engines makes you discoverable for your niche project experience</p>

<div class="feature-icon abs" style="left:469px;top:635px">
  <svg width="32" height="32" viewBox="0 0 32 32" fill="#f37122"><circle cx="9" cy="8" r="4"/><circle cx="23" cy="8" r="4"/><circle cx="16" cy="13" r="4.5"/><path d="M2 22c0-5 3-8 7-8s5 2 5 2v10H2z"/><path d="M30 22c0-5-3-8-7-8s-5 2-5 2v10h12z"/><path d="M8 30c0-6 3-10 8-10s8 4 8 10z"/></svg>
</div>
<h3 class="feature-title abs" style="left:561px;top:645px">LESS INTERVIEWS</h3>
<p class="feature-text abs" style="left:561px;top:664px">Experince fewer interviews with TRAVENOK to get the right job. Our platform matches you against your specilized project experinces, industry exposure and core PM skills</p>

<div class="feature-icon abs" style="left:68px;top:744px">
  <svg width="32" height="32" viewBox="0 0 32 32"><rect x="4" y="4" width="14" height="18" fill="#f37122"/><path d="M11 10 H21 L28 17 V30 H11 Z" fill="#fff" stroke="#f37122" stroke-width="2.5"/><path d="M21 10 V17 H28" fill="none" stroke="#f37122" stroke-width="2"/></svg>
</div>
<h3 class="feature-title abs" style="left:160px;top:754px">TRANSPERENCY</h3>
<p class="feature-text abs" style="left:160px;top:773px">In order to promote win-win scenarios for our clients and consultants, we provide 100% transparency in all our servic-es</p>

<div class="feature-icon abs" style="left:471px;top:748px">
  <svg width="32" height="32" viewBox="0 0 32 32" fill="#f37122"><circle cx="11" cy="17" r="7"/><circle cx="11" cy="17" r="2.5" fill="#fff"/><circle cx="24" cy="9" r="4.5"/><circle cx="24" cy="9" r="1.5" fill="#fff"/><circle cx="24" cy="24" r="4.5"/><circle cx="24" cy="24" r="1.5" fill="#fff"/><g stroke="#f37122" stroke-width="3"><path d="M11 8v18M2 17h18M5 11l12 12M17 11L5 23"/></g><circle cx="11" cy="17" r="2.5" fill="#fff"/></svg>
</div>
<h3 class="feature-title abs" style="left:563px;top:758px">MAKE BETTER DECISIONS</h3>
<p class="feature-text abs" style="left:563px;top:777px">Employers who have considered all their options and care-fully made a decision to join us understand that we bring the highest caliber candidates for the jobs</p>

<section class="upload abs" role="img" aria-label="Blurred photo of a hand selecting a candidate from a network of people"></section>
<svg class="abs" style="left:423px;top:897px" width="32" height="32" viewBox="0 0 32 32" fill="#fff"><path d="M16 1 L24 10 H19 V20 H13 V10 H8 Z"/><rect x="1" y="20" width="30" height="10" rx="2"/><circle cx="23" cy="25" r="1.3" fill="#444"/><circle cx="27" cy="25" r="1.3" fill="#444"/></svg>
<h2 class="upload-title abs">UPLOAD YOUR RESUME</h2>

<footer class="site-footer abs"></footer>
<div class="brand abs" style="left:69px;top:1063px;font-size:19px">TRAVENOK</div>
<div class="footer-tag abs">PROJECT MANAGEMENT CONSULTING</div>

<div class="footer-head abs" style="left:236px">CONTACT US</div>
<p class="footer-text abs" style="left:237px;top:1058px">Address : 12 Fenwyck Lane, Harrow Quay<br>Dunmere, DM4 7QX<br>Phone : 555-014-2290.<br>Email : hello@travenok.example</p>

<div class="footer-head abs" style="left:443px">JOIN OUR MAILING LIST</div>
<p class="footer-text abs" style="left:443px;top:1056px;line-height:12px;width:150px">Your about us information would fit here nicely.</p>
<div class="mail-input abs">Email address</div>
<div class="mail-btn abs">Submit</div>

<div class="footer-head abs" style="left:687px">FOLLOW US OUT THERE</div>
<div class="social abs" style="left:687px" aria-label="Social profile"></div>
<div class="social abs" style="left:715px" aria-label="Social profile"></div>
<div class="social abs" style="left:743px" aria-label="Social profile"></div>
<div class="social abs" style="left:771px" aria-label="Social profile"></div>

<div class="footer-rule abs"></div>
<p class="copyright abs">Copyright © 2016. All Rights Reserved</p>
</body>
</html>
```